Health Care Company with Logo Needs Business Cards designed

We are a luxury behavioral health company looking for business cards design we already have a logo and are looking for someone to design a sophisticated luxurious looking business card. Please note that Card design should be captivating just like the logo and also encompass the logo color

Industry/Entity Type

Healthcare

Contact Information for Business Card

Logo,company name, tagline, my name and title, contact details, and physical address

```html
<!DOCTYPE html>
<html lang="en">
<head>
<meta charset="utf-8">
<title>Orin Behavioral Health – Business Card</title>
<link href="https://fonts.googleapis.com/css2?family=Roboto+Condensed:wght@400;700&family=Roboto:ital,wght@0,400;0,500;1,400&display=swap" rel="stylesheet">
<style>
  :root {
    --backdrop: #2b2b2c;
    --card: #232325;
    --card-edge: #1b1b1d;
    --plum: #7b2d8e;
    --plum-light: #8a3a9c;
    --sky: #1a9ad6;
    --ocean: #0f7fbf;
    --indigo: #4a55a8;
    --ink-light: #e6e6e8;
    --ink-soft: #cfcfd3;
  }
  * { box-sizing: border-box; margin: 0; padding: 0; }
  html, body { width: 1200px; height: 1138px; overflow: hidden; }
  body {
    background: var(--backdrop);
    position: relative;
    font-family: "Roboto", Arial, sans-serif;
  }
  .card {
    position: absolute;
    left: 276px;
    width: 622px;
    height: 374px;
    border-radius: 14px;
    background: var(--card);
    overflow: hidden;
  }
  .card--front { top: 186px; }
  .card--back { top: 608px; }

  .front-accent {
    position: absolute;
    right: -70px;
    top: 40px;
    width: 300px;
    height: 300px;
    border-radius: 50%;
    background: var(--card-edge);
  }
  .brand {
    position: absolute;
    font-family: "Roboto Condensed", Arial Narrow, sans-serif;
  }
  .brand__name {
    font-weight: 700;
    color: var(--plum);
    line-height: 1;
    white-space: nowrap;
  }
  .brand__tagline {
    font-weight: 700;
    text-transform: uppercase;
    white-space: nowrap;
    margin-top: 4px;
  }
  .card--front .brand { left: 40px; top: 170px; }
  .card--front .brand__name { font-size: 24px; }
  .card--front .brand__tagline { font-size: 7.6px; letter-spacing: 1.9px; color: var(--ink-soft); }

  .card--back .brand { right: 29px; top: 38px; text-align: right; }
  .card--back .brand__name { font-size: 27px; }
  .card--back .brand__tagline { font-size: 8.4px; letter-spacing: 2.2px; color: var(--sky); margin-top: 5px; }

  .panel { position: absolute; left: 0; top: 0; width: 300px; height: 374px; }
  .panel-mark {
    position: absolute;
    left: 0;
    top: 162px;
    width: 250px;
    text-align: center;
    font-family: "Roboto Condensed", Arial Narrow, sans-serif;
    font-weight: 700;
    font-size: 44px;
    color: #f2f2f2;
    letter-spacing: 1px;
  }

  .person { position: absolute; right: 29px; top: 148px; text-align: right; }
  .person__name { font-family: "Roboto", Arial, sans-serif; font-weight: 500; font-size: 23px; color: var(--plum-light); line-height: 1; }
  .person__role { font-style: italic; font-size: 15px; color: var(--ink-light); margin-top: 7px; }

  .address { position: absolute; right: 29px; top: 222px; text-align: right; font-size: 15px; line-height: 22px; color: var(--ink-light); }

  .contacts { position: absolute; right: 26px; top: 276px; list-style: none; }
  .contacts li { display: flex; justify-content: flex-end; align-items: center; height: 22px; font-size: 15px; color: var(--ink-light); }
  .contacts svg { width: 14px; height: 14px; margin-left: 18px; }
</style>
</head>
<body>
  <section class="card card--front">
    <div class="front-accent"></div>
    <div class="brand">
      <p class="brand__name">Orin Behavioral Health</p>
      <p class="brand__tagline">Dedicated to hope, healing and recovery</p>
    </div>
  </section>

  <section class="card card--back">
    <svg class="panel" viewBox="0 0 300 374">
      <defs>
        <linearGradient id="panelFill" x1="0" y1="0" x2="0.35" y2="1">
          <stop offset="0" stop-color="#7a3a8c"/>
          <stop offset="0.45" stop-color="#3f63a8"/>
          <stop offset="1" stop-color="#0c7fc0"/>
        </linearGradient>
      </defs>
      <path d="M0 0 H224 Q362 187 220 374 H0 Z" fill="#7b2d8e"/>
      <path d="M0 0 H218 Q354 187 212 374 H0 Z" fill="#1a9ad6"/>
      <path d="M0 0 H214 Q346 187 206 374 H0 Z" fill="url(#panelFill)"/>
    </svg>
    <p class="panel-mark">ORIN</p>

    <div class="brand">
      <p class="brand__name">Orin Behavioral Health</p>
      <p class="brand__tagline">Dedicated to hope, healing and recovery</p>
    </div>

    <div class="person">
      <p class="person__name">DANIEL REEVE</p>
      <p class="person__role">Managing Director</p>
    </div>

    <p class="address">123, Anywhere ST, Any City,<br>Any Town, US 123456</p>

    <ul class="contacts">
      <li>000-111-0000
        <svg viewBox="0 0 14 14"><path d="M2 5c0-2 2-3 5-3s5 1 5 3v1H9V5H5v1H2z M4 7h6l2 5H2z" fill="#5a4fa8"/></svg>
      </li>
      <li>hello@orinbehavioral.com
        <svg viewBox="0 0 14 14"><rect x="1" y="3" width="12" height="8" fill="#5a4fa8"/><path d="M1 3l6 5 6-5" stroke="#232325" stroke-width="1.2" fill="none"/></svg>
      </li>
      <li>www.orinbehavioral.com
        <svg viewBox="0 0 14 14"><circle cx="7" cy="7" r="5.5" fill="#3f6fb4"/><path d="M1.5 7h11M7 1.5c-3 3-3 8 0 11M7 1.5c3 3 3 8 0 11" stroke="#232325" stroke-width="0.8" fill="none"/></svg>
      </li>
    </ul>
  </section>
</body>
</html>
```